Marwick Law Letterhead

We need a new letterhead design for a Law Firm. The address for the law firm is 1475 Calloway Street, Suite 210, Houston, Texas 77041. Phone Number: 832-361-9027; Fax Number: 832-614-7359. The logo is uploaded to the project.

```html
<!DOCTYPE html>
<html lang="en">
<head>
<meta charset="utf-8">
<title>Marwick Law Letterhead</title>
<link rel="stylesheet" href="https://fonts.googleapis.com/css2?family=Tinos:wght@400;700&family=Raleway:wght@400;500;700&display=swap">
<style>
  :root {
    --backdrop: #ebe3d6;
    --paper: #ffffff;
    --navy: #1f3566;
    --red: #e11d25;
    --ink: #2a2a2a;
    --muted: #555555;
  }
  * { box-sizing: border-box; margin: 0; padding: 0; }
  html, body { width: 1200px; height: 1200px; overflow: hidden; }
  body { background: var(--backdrop); position: relative; font-family: "Raleway", sans-serif; }

  .letterhead {
    position: absolute; left: 175px; top: 50px;
    width: 850px; height: 1100px;
    background: var(--paper);
    box-shadow: 0 4px 14px rgba(0,0,0,0.12);
    overflow: hidden;
  }

  .band { position: absolute; left: 0; width: 100%; }
  .band--top-navy { top: 0; height: 14px; background: var(--navy); }
  .band--top-red { top: 20px; height: 4px; background: var(--red); }
  .band--bottom-red { bottom: 22px; height: 4px; background: var(--red); }
  .band--bottom-navy { bottom: 0; height: 14px; background: var(--navy); }

  .brand {
    position: absolute; left: 70px; top: 150px;
    display: flex; align-items: center; gap: 14px;
  }
  .brand__mark { width: 22px; height: 22px; background: var(--navy); }
  .brand__name {
    font-family: "Tinos", serif; font-weight: 400;
    font-size: 40px; letter-spacing: 1px; color: var(--navy);
  }

  .firm-contact {
    position: absolute; right: 70px; top: 66px;
    text-align: right; font-style: normal;
    font-family: "Tinos", serif; font-size: 14px; line-height: 1.3;
    color: var(--navy);
  }

  .letter {
    position: absolute; left: 150px; top: 290px; width: 500px;
    color: var(--ink); font-size: 12.5px; line-height: 1.7;
  }
  .recipient { margin-bottom: 28px; }
  .recipient__line { font-weight: 700; line-height: 1.35; }
  .recipient__phone { font-weight: 400; color: var(--muted); font-size: 14px; }
  .salutation { font-weight: 700; margin-bottom: 14px; }
  .letter__para { margin-bottom: 22px; text-align: justify; }
  .sign-off__name { font-weight: 700; line-height: 1.3; }
  .sign-off__title { line-height: 1.3; }
  .sign-off__signature {
    width: 120px; height: 36px; margin-top: 6px; margin-left: 60px;
    background: linear-gradient(90deg, #ececec, #dadada);
    border-radius: 4px;
  }
</style>
</head>
<body>
  <main class="letterhead">
    <div class="band band--top-navy" aria-hidden="true"></div>
    <div class="band band--top-red" aria-hidden="true"></div>

    <div class="brand">
      <span class="brand__mark"></span>
      <span class="brand__name">MARWICK LAW</span>
    </div>

    <address class="firm-contact">
      1475 Calloway Street,<br>
      Suite 210, Houston,<br>
      Texas 77041<br>
      Tel: 832-361-9027<br>
      Fax: 832-614-7359
    </address>

    <article class="letter">
      <div class="recipient">
        <p class="recipient__line">418 Linden Crest Road</p>
        <p class="recipient__line">Pasadena, CA 91104</p>
        <p class="recipient__phone">626-507-3148</p>
      </div>
      <p class="salutation">Dear Mr. Ortega</p>
      <p class="letter__para">Fusce scelerisque sem sem, non interdum ligula gravida id. Curabitur sit amet molestie elit. Pellentesque ac congue diam. Duis varius suscipit elementum. Ut ac volutpat arcu, id commodo erat. Suspendisse tempor diam ut nunc egestas finibus. Maecenas quis porttitor dolor, a accumsan odio. Phasellus nisl metus, consectetur ut venenatis sit amet, imperdiet at nunc.</p>
      <p class="letter__para">Donec facilisis malesuada ipsum sit amet vulputate. Integer justo justo, fermentum vitae pellentesque feugiat, ullamcorper non velit. Suspendisse molestie volutpat nisl at faucibus. Praesent posuere sodales libero, sed lacinia lacus ultrices eu. Phasellus lobortis, lectus sit amet vehicula hendrerit, risus purus blandit nunc, porttitor dictum arcu nisl varius ipsum. Nam tempus et purus sit amet cursus. Ut nec mauris quam. Integer condimentum quis magna id tempus. Pellentesque et orci scelerisque nisi faucibus egestas et at orci. Aliquam placerat ultricies erat id tincidunt. Nunc quis justo ipsum. Pellentesque at nisl et nulla posuere sollicitudin vitae vel ex. Vivamus fermentum orci sem. Phasellus tempor, metus vitae rutrum varius, ex libero mattis sapien, nec dictum enim augue non augue. Vestibulum in orci ut augue iaculis porttitor.</p>
      <p class="letter__para">Praesent sit amet augue auctor, ultrices dui eget, pellentesque enim. Vivamus eu elementum odio. Nulla vitae enim porta, posuere tellus in, euismod nulla. Pellentesque vitae sodales ligula, vitae viverra nunc. Integer tristique sit amet leo vel feugiat.</p>
      <div class="sign-off">
        <p class="sign-off__name">Daniel R. Whitfield</p>
        <p class="sign-off__title">Marketing Manager</p>
        <div class="sign-off__signature" role="img" aria-label="Handwritten signature of the sender"></div>
      </div>
    </article>

    <div class="band band--bottom-red" aria-hidden="true"></div>
    <div class="band band--bottom-navy" aria-hidden="true"></div>
  </main>
</body>
</html>
```